Start-Up für Training, Coaching & Consulting sucht modernes Webdesign!
Zielgruppe
Wer ist TAVI Training, Coaching & Consulting?
Wir führen Führungskräftetrainings durch, machen Privatkunden für Bewerbungen fit und unterstützen Unternehmen mit Verkaufstrainings. Wir entwickeln Persönlichkeiten im Coaching. Wir beraten Unternehmen und helfen ihnen dabei, ihre Geschäftsabläufe und Prozesse zu optimieren. Dabei steht unsere hohe Qualität im Mittelpunkt - gemeinsam mit unseren kreativen Trainingsmethoden. Unser Background (Diplom-Kaufleute und geprüfte Trainer) bietet dafür die passende Ausgangslage.
Was bedeutet TAVI?
Tavi ist Maori und bdeutet Kreis/Spirale. Er symbolisiert einen wachsenden Silberfarn und steht für persönliche Entwicklung und Entfaltung. Der Tavi ist einerseits unser Namensgeber und unser Logo, andererseits steht der Tavi aber auch für unsere Werte: Denn wir wollen unseren Kunden dabei helfen zu wachsen und sich weiterzuentwickeln - und dies auf eine hochqualitative und seriöse Art und Weise ohne den Eindruck von Esoterik oder Erlebnispädagogik zu vermitteln.
Aufgabenstellung
Modernes Design, das unsere Philosophie widerspiegelt: Wir möchten unseren Kunden auf seriöse und hochqualitative Weise weiterentwickeln. Wir stehen für nachhaltigen Lernerfolg, kreative Trainingsmethoden, Abwechslung, Spaß am Lernen, Qualität, Kompetenz, Fachwissen und Dynamik.
Layout:
1) Header: QMSR geprüfter Trainer, Menüpunkte (siehe Architektur)
2) Banner
3) 3 Teaser (Training, Coaching, Consulting) + Header + 2-3 Zeilen Text (+Icons)
>>> Sichtbarer Bereich auf Homepage: Menü, Banner, Teaser
4) "Warum Sie uns wählen sollten": 5 bullet points ohne weiteren Text
5) "Aus unserem Blog": Frame für 3 Blogartikel + Bild + Datum + Header + 2-3 Zeilen Text
6) Alle drei QMSR Logos
7) Footer: Click Us (quick links), Contact Us (Adresse), Follow Us (Pinnwald, ZOLP, Kontaktor)
8) Copyright + Impressum
>>> Das Design soll klar sein, aber nicht zu kantig. Vielmehr sollen abgerundete Ecken und dynamische Elemente genutzt werden.
Architektur:
3 Ebenen:
1) Homepage
2) TAVI, Training, Coaching, Consulting, für Trainer, Kundenstimmen/Referenzen, Kontakt
3) noch zu bestimmende Produktdetailseiten
Texte werden noch erstellt, Layout kann ggf. mit Platzhaltertext gefüllt werden.
Bildmaterial: Logo und vorhandenes Imagebild werden zur Verfügung gestellt. Bilder können ggf. gekauft werden. Vorschläge erwünscht.
Corporate colors:
grün: #a2c61b + monochromatic colors
http://www.tintoskop.de/a2c61b
grau: #474747 + monochromatic colors
http://www.tintoskop.de/474747

```html
<!DOCTYPE html>
<html lang="en">
<head>
<meta charset="utf-8">
<title>TAVI Training, Coaching & Consulting</title>
<link href="https://fonts.googleapis.com/css2?family=Jost:wght@500;600;700&family=Questrial&display=swap" rel="stylesheet">
<style>
:root{
  --green:#a2c61b;
  --green-dark:#8fb012;
  --grey:#474747;
  --ink:#2e2e2e;
  --text:#555;
  --nav-bg:#f4f4f4;
  --dark:#262a2e;
  --footer:#2b2b2b;
  --logo-bg:#dcdcdc;
  --badge:#1667c2;
  --white:#fff;
}
*{margin:0;padding:0;box-sizing:border-box}
html,body{width:774px;height:1200px;overflow:hidden}
body{position:relative;background:var(--white);font-family:"Questrial",sans-serif;color:var(--ink)}
.abs{position:absolute}
.top-bar{left:0;top:0;width:774px;height:17px;background:var(--green)}
.brand{left:152px;top:0;width:169px;height:79px;background:var(--white);box-shadow:0 0 6px rgba(0,0,0,.08);text-align:center}
.brand-name{display:block;margin-top:8px;font-family:"Jost",sans-serif;font-weight:700;font-size:38px;line-height:44px;color:var(--grey);letter-spacing:1px}
.brand-tag{display:block;font-size:8.5px;color:var(--grey);border-top:1px solid var(--green);margin:2px 14px 0;padding-top:3px}
.brand-tag b{color:var(--green)}
.contact-top{top:37px;height:19px;display:flex;align-items:center;font-size:9.5px;color:var(--ink)}
.icon-ring{width:18px;height:18px;border:1px solid var(--green);border-radius:50%;display:flex;align-items:center;justify-content:center;margin-right:7px}
.nav{left:0;top:79px;width:774px;height:28px;background:var(--nav-bg)}
.nav a{position:absolute;top:9px;font-size:6.8px;color:var(--ink);text-decoration:none}
.hero{left:0;top:107px;width:774px;height:268px;background:radial-gradient(ellipse at 48% 40%,#6f9a3c 0%,#3f6d2a 40%,#22401d 75%,#1b3318 100%)}
.hero-title{left:0;top:160px;width:774px;text-align:center;font-family:"Jost",sans-serif;font-weight:600;font-size:25px;color:var(--white)}
.hero-title b{color:var(--green)}
.hero-text{left:185px;top:200px;width:404px;text-align:center;font-size:8.6px;line-height:15px;color:var(--white)}
.hero-btn{left:324px;top:264px;width:126px;height:23px;background:var(--green);color:var(--white);font-family:"Jost",sans-serif;font-weight:600;font-size:8.5px;display:flex;align-items:center;justify-content:center}
.hero-arrow{top:215px;width:29px;height:29px;border-radius:50%;background:rgba(0,0,0,.25);color:var(--white);font-size:9px;display:flex;align-items:center;justify-content:center}
.hero-arrow.next{color:var(--green)}
.teaser{top:400px;width:144px;text-align:center}
.teaser-frame{height:90px;border:1px solid #ddd;padding:4px;background:var(--white)}
.teaser-photo{width:100%;height:100%}
.teaser-icon{position:absolute;left:55px;top:73px;width:33px;height:33px;border:1px solid var(--green);border-radius:50%;background:var(--white);display:flex;align-items:center;justify-content:center}
.teaser h2{margin-top:25px;font-family:"Jost",sans-serif;font-weight:600;font-size:9.5px;color:var(--green)}
.teaser p{margin-top:8px;padding:0 8px;font-size:6.6px;line-height:12px;color:var(--text)}
.read-more{display:inline-block;margin-top:8px;border:1px solid #999;padding:2px 7px;font-family:"Jost",sans-serif;font-weight:600;font-size:5.5px;color:var(--ink)}
.why{left:0;top:641px;width:774px;height:234px;background:linear-gradient(100deg,#2b3038 0%,#1f242b 50%,#2f343b 100%)}
.notch{left:370px;top:640px}
.why-title{left:195px;top:738px;font-family:"Jost",sans-serif;font-weight:600;font-size:20px;line-height:25px;color:var(--white)}
.why-title span{color:var(--green)}
.why-list{left:383px;top:688px;list-style:none}
.why-list li{display:flex;align-items:center;height:21px;font-size:7.5px;color:var(--white)}
.why-list svg{margin-right:10px}
.members{left:0;top:875px;width:774px;height:150px;background:var(--logo-bg)}
.badge{background:var(--badge)}
.footer{left:0;top:1000px;width:774px;height:170px}
.footer h3{position:absolute;top:1062px;font-family:"Jost",sans-serif;font-weight:600;font-size:8.5px;color:var(--white)}
.footer-link{font-size:6.8px;color:var(--white)}
.social{top:1078px;display:flex;gap:5px}
.social span{height:16px;padding:0 4px;border:1px solid var(--green);border-radius:2px;font-size:6.5px;color:var(--white);display:flex;align-items:center}
.contact-line{display:flex;align-items:flex-start;font-size:6.8px;line-height:9px;color:var(--white)}
.contact-line svg{margin:1px 9px 0 0;flex:none}
.copyright{left:0;top:1172px;width:774px;height:28px;background:var(--green);color:var(--white);font-size:7.5px;display:flex;align-items:center;justify-content:center}
</style>
</head>
<body>
<div class="abs top-bar"></div>
<div class="abs brand">
  <span class="brand-name">TAVI</span>
  <span class="brand-tag">Training <b>•</b> Coaching <b>•</b> Consulting</span>
</div>
<div class="abs contact-top" style="left:394px">
  <span class="icon-ring"><svg width="9" height="7" viewBox="0 0 9 7"><rect x=".5" y=".5" width="8" height="6" fill="none" stroke="#a2c61b"/><path d="M.5 .5 4.5 4 8.5 .5" fill="none" stroke="#a2c61b"/></svg></span>info@tavitraining.com
</div>
<div class="abs contact-top" style="left:519px">
  <span class="icon-ring"><svg width="9" height="9" viewBox="0 0 10 10"><path d="M2 1 4 3 3 4.5Q4.5 6.5 5.5 7L7 6l2 2-1.5 1.5Q4 9 .5 3Z" fill="#a2c61b"/></svg></span>604.555.0187 FREE
</div>

<nav class="abs nav">
  <a style="left:160px">Home</a><a style="left:208px">Training</a><a style="left:259px">Coaching</a><a style="left:319px">Consulting</a><a style="left:380px">Products</a><a style="left:435px">Fr Trainer</a><a style="left:490px">Customer Testimonials</a><a style="left:587px">Contact</a>
</nav>

<section class="abs hero" role="img" aria-label="Close-up photograph of an unfurling green fern frond"></section>
<svg class="abs" style="left:0;top:325px" width="774" height="50" viewBox="0 0 774 50">
  <path d="M0 27 Q180 45 380 22 Q600 -2 774 22 V50 H0Z" fill="#fff"/>
  <path d="M0 27 Q180 45 380 22 Q600 -2 774 22" fill="none" stroke="#a2c61b" stroke-width="4"/>
</svg>
<h1 class="abs hero-title">TRAINING <b>•</b> COACHING <b>•</b> CONSULTING</h1>
<p class="abs hero-text">Lorem ipsum dolor sit amet, consectetur adipisicing elit, sed do eiusmod tempor incididunt ut labore et dolore magna aliqua. Ut enim ad minim veniam, quis nostrud exercitation ullamco laboris nisi ut aliquip ex ea commodo consequat.</p>
<div class="abs hero-btn">GET CONTACT US NOW</div>
<div class="abs hero-arrow" style="left:62px">&#8249;</div>
<div class="abs hero-arrow next" style="left:683px">&#8250;</div>

<article class="abs teaser" style="left:153px">
  <div class="teaser-frame"><div class="teaser-photo" role="img" aria-label="Photo of a trainer presenting to a group at a meeting table" style="background:linear-gradient(90deg,#c9ccd2,#8d97a6 55%,#4a6fb8)"></div></div>
  <div class="teaser-icon"><svg width="13" height="13" viewBox="0 0 13 13" fill="none" stroke="#777"><rect x="4" y="1" width="8" height="5"/><circle cx="2.5" cy="4" r="1.3"/><path d="M1 12V7h3v5M5 12V9h6v3"/></svg></div>
  <h2>TRAINING</h2>
  <p>This is Studio's version of Lorem Ipsum. Proin gravida nibh vel velit auctor aliquet.</p>
  <span class="read-more">READ MORE</span>
</article>
<article class="abs teaser" style="left:315px">
  <div class="teaser-frame"><div class="teaser-photo" role="img" aria-label="Photo of a hand drawing a glowing growth curve on a dark board" style="background:linear-gradient(100deg,#1c2b34,#2c4452 60%,#4b5a62)"></div></div>
  <div class="teaser-icon"><svg width="13" height="13" viewBox="0 0 13 13" fill="#a2c61b"><circle cx="6.5" cy="3.5" r="2"/><circle cx="2.5" cy="5" r="1.6"/><circle cx="10.5" cy="5" r="1.6"/><path d="M3.5 11a3 3 0 0 1 6 0Z M0 10a2.5 2.5 0 0 1 4 -2L3 10Z M13 10a2.5 2.5 0 0 0-4-2l1 2Z"/></svg></div>
  <h2>COACHING</h2>
  <p>This is Studio's version of Lorem Ipsum. Proin gravida nibh vel velit auctor aliquet.</p>
  <span class="read-more">READ MORE</span>
</article>
<article class="abs teaser" style="left:477px">
  <div class="teaser-frame"><div class="teaser-photo" role="img" aria-label="Photo of two business consultants talking at a desk" style="background:linear-gradient(90deg,#5e6166,#d9dde2 50%,#2f4468)"></div></div>
  <div class="teaser-icon"><svg width="13" height="13" viewBox="0 0 13 13" fill="#777"><circle cx="9" cy="3" r="2"/><path d="M5.5 10a3.5 3.5 0 0 1 7 0Z"/><circle cx="3.5" cy="6" r="1.6"/><path d="M0.5 12a3 3 0 0 1 6 0Z"/></svg></div>
  <h2>CONSULTING</h2>
  <p>This is Studio's version of Lorem Ipsum. Proin gravida nibh vel velit auctor aliquet.</p>
  <span class="read-more">READ MORE</span>
</article>

<section class="abs why" role="img" aria-label="Dark-toned photo of business people shaking hands"></section>
<svg class="abs notch" width="35" height="12" viewBox="0 0 35 12"><path d="M0 0H35L17.5 12Z" fill="#fff"/></svg>
<h2 class="abs why-title">WHY SHOULD<br><span>CHOOS US</span></h2>
<ul class="abs why-list">
  <li><svg width="8" height="8" viewBox="0 0 8 8"><circle cx="4" cy="4" r="3.5" fill="none" stroke="#fff" stroke-width=".7"/><path d="M3.3 2.5 4.8 4 3.3 5.5" fill="none" stroke="#fff" stroke-width=".7"/></svg>Lorem ipsum dolor sit amet, consectetur adipisicing elit</li>
  <li><svg width="8" height="8" viewBox="0 0 8 8"><circle cx="4" cy="4" r="3.5" fill="none" stroke="#fff" stroke-width=".7"/><path d="M3.3 2.5 4.8 4 3.3 5.5" fill="none" stroke="#fff" stroke-width=".7"/></svg>Sed do eiusmod tempor incididunt ut labore et dolore magna</li>
  <li><svg width="8" height="8" viewBox="0 0 8 8"><circle cx="4" cy="4" r="3.5" fill="none" stroke="#fff" stroke-width=".7"/><path d="M3.3 2.5 4.8 4 3.3 5.5" fill="none" stroke="#fff" stroke-width=".7"/></svg>aliqua. Ut enim ad minim veniam,</li>
  <li><svg width="8" height="8" viewBox="0 0 8 8"><circle cx="4" cy="4" r="3.5" fill="none" stroke="#fff" stroke-width=".7"/><path d="M3.3 2.5 4.8 4 3.3 5.5" fill="none" stroke="#fff" stroke-width=".7"/></svg>Quis nostrud exercitation ullamco laboris nisi ut</li>
  <li><svg width="8" height="8" viewBox="0 0 8 8"><circle cx="4" cy="4" r="3.5" fill="none" stroke="#fff" stroke-width=".7"/><path d="M3.3 2.5 4.8 4 3.3 5.5" fill="none" stroke="#fff" stroke-width=".7"/></svg>Aliquip ex ea commodo consequat.</li>
  <li><svg width="8" height="8" viewBox="0 0 8 8"><circle cx="4" cy="4" r="3.5" fill="none" stroke="#fff" stroke-width=".7"/><path d="M3.3 2.5 4.8 4 3.3 5.5" fill="none" stroke="#fff" stroke-width=".7"/></svg>Duis aute irure dolor in reprehenderit in voluptate velit</li>
  <li><svg width="8" height="8" viewBox="0 0 8 8"><circle cx="4" cy="4" r="3.5" fill="none" stroke="#fff" stroke-width=".7"/><path d="M3.3 2.5 4.8 4 3.3 5.5" fill="none" stroke="#fff" stroke-width=".7"/></svg>Esse cillum dolore eu fugiat nulla pariatur.</li>
</ul>

<section class="abs members" aria-label="Memberships"></section>
<div class="abs badge" style="left:167px;top:917px;width:42px;height:56px"></div>
<div class="abs badge" style="left:317px;top:917px;width:43px;height:56px"></div>
<div class="abs badge" style="left:485px;top:927px;width:122px;height:32px"></div>

<div class="abs footer" style="background:var(--footer)"></div>
<svg class="abs" style="left:0;top:1000px" width="774" height="45" viewBox="0 0 774 45">
  <path d="M0 0H774V38 Q560 46 380 22 Q200 -2 0 24Z" fill="#dcdcdc"/>
  <path d="M0 24 Q200 -2 380 22 Q560 46 774 38" fill="none" stroke="#a2c61b" stroke-width="4"/>
</svg>
<div class="footer">
  <h3 style="left:153px">QUICK LINKS</h3>
  <h3 style="left:342px">FOLLOW US</h3>
  <h3 style="left:484px">CONTACT US</h3>
</div>
<div class="abs footer-link" style="left:153px;top:1085px;line-height:17px">Home<br>Training<br>Coaching<br>Consulting</div>
<div class="abs footer-link" style="left:209px;top:1085px;line-height:17px">Products<br>Fr Trainer<br>Customer Testimonials<br>Contact</div>
<div class="abs social" style="left:342px"><span>Pinnwald</span><span>ZOLP</span><span>Kontaktor</span></div>
<div class="abs contact-line" style="left:486px;top:1085px"><svg width="5" height="7" viewBox="0 0 5 7"><path d="M2.5 7 .5 3.5a2 2 0 1 1 4 0Z" fill="#fff"/><circle cx="2.5" cy="2.5" r=".8" fill="#2b2b2b"/></svg><span>#410, 2280 Alder Street<br>Fernvale, BC V3K 2L9</span></div>
<div class="abs contact-line" style="left:486px;top:1115px"><svg width="6" height="6" viewBox="0 0 10 10"><path d="M2 1 4 3 3 4.5Q4.5 6.5 5.5 7L7 6l2 2-1.5 1.5Q4 9 .5 3Z" fill="#fff"/></svg><span>604.555.0187 FREE</span></div>
<div class="abs contact-line" style="left:486px;top:1131px"><svg width="6" height="5" viewBox="0 0 9 7"><rect width="9" height="7" fill="#fff"/><path d="M0 0 4.5 4 9 0" fill="none" stroke="#2b2b2b"/></svg><span>info@tavitraining.com</span></div>

<footer class="abs copyright">Tavi © 2015 | All Rights Reserved</footer>
</body>
</html>
```